Sell the dream! Property investment proposal document

We are looking for a proposal document which outlines our vision for property development. The purpose of the document is to raise investment from investors - sell the dream!
Brief summary:
Kestrel Dwellings Developments, is an emerging New Zealand property investment company with a focus on providing unique property investment opportunities.
Our expertise and capabilities in architectural modular homes provide us with a remarkable advantage in tackling the development of properties that are typically considered challenging, remote, or uniquely positioned.
Our specialization in this niche sector of property development not only sets us apart from competitors, but also paves the way for lucrative investment opportunities in the New Zealand property market.
Feel free to use any images from www.kestreldwellings.co.nz
Target Market(s)
investors for a unique property development opportunity
Industry/Entity Type
luxury property development in unique locations throughout New Zealand
Colors
Designer to choose only greyscale colors for use in the design.
Look and feel

```html
<!DOCTYPE html>
<html lang="en">
<head>
<meta charset="utf-8">
<title>Kestrel Dwellings Developments – Investment Proposal</title>
<link href="https://fonts.googleapis.com/css2?family=Poppins:wght@300;400;500;700&display=swap" rel="stylesheet">
<style>
  :root {
    --canvas: #e9eef4;
    --paper: #ffffff;
    --ink: #111111;
    --text: #2a2a2a;
    --cover-sky: #eef0f2;
    --shadow: rgba(0,0,0,0.18);
  }
  * { box-sizing: border-box; margin: 0; padding: 0; }
  html, body { width: 1200px; height: 546px; overflow: hidden; }
  body { background: var(--canvas); font-family: "Poppins", sans-serif; color: var(--text); position: relative; }

  .page { position: absolute; top: 44px; width: 324px; height: 457px; background: var(--paper); box-shadow: 0 6px 18px var(--shadow); overflow: hidden; }
  .page--cover { left: 73px; background: linear-gradient(180deg, #e4e7ea 0%, var(--cover-sky) 45%, #f3f4f5 55%); }
  .page--overview { left: 438px; }
  .page--origins { left: 804px; }

  .brand-word { position: absolute; left: 15px; top: 38px; font-size: 48px; font-weight: 400; line-height: 1; letter-spacing: -1.5px; color: var(--ink); }
  .contact-box { position: absolute; right: 0; top: 0; width: 119px; height: 59px; background: var(--ink); color: #fff; padding: 11px 0 0 12px; }
  .contact-label { display: flex; align-items: center; gap: 10px; font-size: 9px; letter-spacing: 3.2px; font-weight: 400; }
  .contact-label svg { width: 11px; height: 11px; }
  .contact-number { font-size: 15.5px; font-weight: 700; margin-top: 4px; letter-spacing: 0.2px; }

  .cover-title { position: absolute; left: 16px; top: 110px; font-size: 16.5px; font-weight: 700; color: var(--ink); letter-spacing: -0.2px; }
  .cover-lede { position: absolute; left: 17px; top: 133px; width: 300px; font-size: 11px; line-height: 16.3px; color: var(--ink); }
  .cover-photo { position: absolute; left: 0; top: 240px; width: 100%; height: 217px;
    background: linear-gradient(180deg, #3c3c3a 0%, #262624 35%, #4a4a44 65%, #8f8a6e 85%, #a39a78 100%); }

  .section-title { position: absolute; left: 11px; top: 14px; font-size: 12px; font-weight: 700; color: var(--ink); letter-spacing: -0.1px; }
  .body-copy { position: absolute; font-size: 6px; line-height: 9.4px; letter-spacing: -0.05px; color: var(--text); }
  .body-copy p + p { margin-top: 4px; }

  .photo { position: absolute; }
  .photo--coast-estate { left: 12px; top: 60px; width: 301px; height: 173px;
    background: linear-gradient(180deg, #9a958a 0%, #6b6a5c 25%, #4d4a2e 55%, #5a5a32 80%, #3a3a2a 100%); }
  .photo--lounge-view { left: 12px; top: 324px; width: 135px; height: 97px;
    background: linear-gradient(180deg, #d6dde2 0%, #a8b4b8 40%, #8a9272 65%, #6e5a44 100%); }
  .photo--glass-pavilion { left: 40px; top: 74px; width: 100px; height: 149px;
    background: linear-gradient(180deg, #9fb2c4 0%, #c8ccc8 45%, #b0a590 65%, #6a655e 100%); }
  .photo--cantilever { left: 159px; top: 72px; width: 121px; height: 151px;
    background: linear-gradient(180deg, #e6ecf0 0%, #d5dde3 45%, #4a4c50 60%, #6c8a3e 80%, #5a7a2e 100%); }
  .photo--framed-vista { left: 174px; top: 301px; width: 134px; height: 125px;
    background: linear-gradient(180deg, #d9dfe3 0%, #b3c0c6 40%, #7e8d6a 62%, #6b5844 100%); }

  .footer-bar { position: absolute; left: 0; top: 432px; width: 262px; height: 20px; background: var(--ink); color: #fff; font-size: 5px; padding: 7px 0 0 10px; }
  .footer-word { position: absolute; left: 268px; top: 432px; font-size: 12.5px; line-height: 20px; font-weight: 400; color: var(--ink); letter-spacing: -0.3px; }
</style>
</head>
<body>

  <section class="page page--cover">
    <div class="brand-word">Kestrel</div>
    <div class="contact-box">
      <div class="contact-label">
        <svg viewBox="0 0 24 24" aria-hidden="true"><path fill="#fff" d="M6.6 10.8a15.1 15.1 0 0 0 6.6 6.6l2.2-2.2a1 1 0 0 1 1-.25 11.4 11.4 0 0 0 3.6.57 1 1 0 0 1 1 1V20a1 1 0 0 1-1 1A17 17 0 0 1 3 4a1 1 0 0 1 1-1h3.5a1 1 0 0 1 1 1c0 1.25.2 2.45.57 3.57a1 1 0 0 1-.25 1z"/></svg>
        REACH US
      </div>
      <div class="contact-number">09 555 0142</div>
    </div>
    <h1 class="cover-title">Modular architectural homes</h1>
    <p class="cover-lede">Architecturally-designed, highly customisable homes, built off-site, delivered to and connected on your own, personal plot of land anywhere in New Zealand.</p>
    <div class="cover-photo" role="img" aria-label="Dark modular home with glass walls, covered outdoor dining area and tall grasses in front"></div>
  </section>

  <section class="page page--overview">
    <h2 class="section-title">Business Overview</h2>
    <div class="body-copy" style="left:12px; top:36px; width:302px;">
      <p>Kestrel Dwellings Developments, is an emerging New Zealand property investment company with a focus on providing unique property investment opportunities.</p>
    </div>
    <div class="photo photo--coast-estate" role="img" aria-label="Low dark timber home on green coastal hills above the sea at sunset"></div>
    <div class="body-copy" style="left:12px; top:248px; width:302px;">
      <p>Our expertise and capabilities in architectural modular homes provide us with a remarkable advantage in tackling the development of properties that are typically considered challenging, remote, or uniquely positioned.</p>
      <p>As a company, with 48 employees boasting a wealth of experience in handling complex architectural projects, making us well-equipped to navigate the intricacies and demands of such ventures.</p>
    </div>
    <div class="photo photo--lounge-view" role="img" aria-label="Interior with floor-to-ceiling glass framing hills and a bay"></div>
    <div class="body-copy" style="left:157px; top:325px; width:157px;">
      <p>This advantage allows us to not only execute projects efficiently but also to deliver exceptional results within condensed time frames.</p>
      <p>By capitalizing on our ability to develop difficult, remote, or one-of-a-kind properties swiftly and effectively, Kestrel Dwellings Developments offers investors a rare chance to engage in projects that promise exceptional profitability in the New Zealand property market.</p>
    </div>
    <div class="footer-bar">Page 01</div>
    <div class="footer-word">Kestrel</div>
  </section>

  <section class="page page--origins">
    <h2 class="section-title">Business Origins</h2>
    <div class="body-copy" style="left:12px; top:36px; width:302px;">
      <p>Kestrel Dwellings Developments was established with the goal of transforming the property investment market in New Zealand by introducing an innovative approach that centers on architectural modular designs and streamlined project timelines.</p>
    </div>
    <div class="photo photo--glass-pavilion" role="img" aria-label="Glass pavilion on a gravel shore facing the sea at dusk"></div>
    <div class="photo photo--cantilever" role="img" aria-label="Dark cantilevered home over a grassy, rocky hillside by the sea"></div>
    <div class="body-copy" style="left:12px; top:236px; width:304px;">
      <p>Driven by our enthusiasm for architecture and real estate, we have expanded our successful business model to not only offer financial opportunities for investors but also to expand on our passion for high-end architectural design.</p>
      <p>With a wealth of experience accumulated over the past six years in the construction and the property market, we are pivoting to focus solely on our property development initiatives, presenting completed Kestrel projects to the market, in exclusive locations.</p>
    </div>
    <div class="body-copy" style="left:12px; top:306px; width:156px;">
      <p>These projects will boast high-quality standards, meticulous attention to detail and landscaping, and creative design elements.</p>
      <p>By introducing completed Kestrel properties into the market, we aim to reach a wider audience, catering to individuals who prefer ready-to-occupy homes, over engaging in the design and construction process. This approach also simplifies the financing process for prospective buyers, as established properties are often preferred by financial lenders.</p>
    </div>
    <div class="photo photo--framed-vista" role="img" aria-label="Wide glazed opening looking over green hills to a harbour"></div>
    <div class="footer-bar">Page 03</div>
    <div class="footer-word">Kestrel</div>
  </section>

</body>
</html>
```